Our new beauty salon requires a price list brochure

Our beauty clinic is a medical grade skin care clinic. So our salon is very clinical and professional in appearance. I would like the colours to be similar to our logo design with some nice texture or abstract shapes thrown in.
Pricelist, contact details and logo is attached
I would prefer it to be a 3 fold brochure.

Target Market(s)

Females aged 30-50

Colors
85acd3
cedeed
c4c4c4
5c5c5c
000000
ffffff
eea3c7
f9d9e8
dbdbdb

Requirements
Must have
• easy to read

```html
<!DOCTYPE html>
<html lang="en">
<head>
<meta charset="utf-8">
<title>Maren Aesthetics – Price List</title>
<link href="https://fonts.googleapis.com/css2?family=Lato:wght@300;400;700&display=swap" rel="stylesheet">
<style>
  :root {
    --slate: #536472;
    --slate-deep: #4b5b68;
    --ink: #f3f5f7;
    --leader: rgba(243,245,247,0.75);
    --skin-light: #e9c2a8;
    --skin-mid: #c99677;
    --row: 21.5px;
  }
  * { margin: 0; padding: 0; box-sizing: border-box; }
  html, body { width: 1200px; height: 941px; overflow: hidden; }
  body {
    background: var(--slate);
    font-family: "Lato", Arial, sans-serif;
    color: var(--ink);
    position: relative;
  }
  .brochure { position: relative; width: 1200px; height: 941px; }

  .brand {
    position: absolute; top: 34px; width: 274px;
    text-align: center; font-weight: 300; color: var(--ink);
    border-bottom: 3px solid var(--ink); padding-bottom: 12px;
  }
  .brand-name { display: block; font-size: 60px; line-height: 66px; letter-spacing: 2px; }
  .brand-sub { display: block; font-size: 10px; letter-spacing: 8px; margin-top: 8px; }

  .heading {
    position: absolute; font-weight: 700; font-size: 26px; line-height: 28px;
    letter-spacing: 0.2px;
  }

  .price-list { position: absolute; list-style: none; font-size: 17px; }
  .price-list li {
    display: flex; align-items: baseline; height: var(--row); line-height: var(--row);
  }
  .price-list li.gap { height: var(--row); }
  .item { white-space: nowrap; }
  .leader {
    flex: 1; margin: 0 6px; border-bottom: 1.5px dashed var(--leader);
    transform: translateY(-5px);
  }
  .price { white-space: nowrap; }
  .price-list.left { left: 52px; width: 301px; }
  .price-list.left .price { width: 44px; }
  .price-list.mid { left: 443px; width: 318px; }
  .price-list.mid .price { width: 33px; }
  .price-list.right { left: 829px; width: 320px; }
  .price-list.right .price { width: 36px; }

  .price-list.treatments { left: 829px; width: 331px; font-weight: 700; top: 325px; }
  .price-list.treatments .price { width: 52px; }
  .price-list.treatments .duration { width: 54px; white-space: nowrap; }

  .injectables {
    position: absolute; left: 829px; width: 334px; top: 424px;
    text-align: center; font-size: 17px; line-height: var(--row);
  }

  .photo {
    position: absolute; left: 800px; top: 522px; width: 400px; height: 352px;
    background:
      radial-gradient(ellipse 36% 50% at 55% 55%, var(--skin-light) 0%, var(--skin-mid) 55%, rgba(83,100,114,0) 100%);
  }
  .fillers-band {
    position: absolute; left: 792px; top: 874px; width: 408px; height: 51px;
    background: var(--slate-deep); display: flex; align-items: center; justify-content: center;
    font-size: 17px;
  }
  .skin-strip {
    position: absolute; left: 760px; top: 925px; width: 440px; height: 16px;
    background: linear-gradient(90deg, rgba(233,194,168,0), var(--skin-light) 40%, var(--skin-mid));
  }
</style>
</head>
<body>
<main class="brochure">

  <!-- Panel 1 -->
  <div class="brand" style="left:74px"><span class="brand-name">maren</span><span class="brand-sub">AESTHETICS</span></div>
  <h2 class="heading" style="left:55px; top:176px">IPL HAIR REMOVAL</h2>
  <ul class="price-list left" style="top:217px">
    <li><span class="item">Upper lip</span><span class="leader"></span><span class="price">$50</span></li>
    <li><span class="item">Chin</span><span class="leader"></span><span class="price">$50</span></li>
    <li><span class="item">Cheeks</span><span class="leader"></span><span class="price">$75</span></li>
    <li><span class="item">Whole face</span><span class="leader"></span><span class="price">$350</span></li>
    <li class="gap"></li>
    <li><span class="item">Bikini</span><span class="leader"></span><span class="price">$90</span></li>
    <li><span class="item">G String</span><span class="leader"></span><span class="price">$120</span></li>
    <li><span class="item">Brazilian</span><span class="leader"></span><span class="price">$150</span></li>
    <li class="gap"></li>
    <li><span class="item">Underarms</span><span class="leader"></span><span class="price">$90</span></li>
    <li><span class="item">Half arm</span><span class="leader"></span><span class="price">$180</span></li>
    <li><span class="item">Full arm</span><span class="leader"></span><span class="price">$250</span></li>
    <li><span class="item">Half leg</span><span class="leader"></span><span class="price">$290</span></li>
    <li><span class="item">Thighs</span><span class="leader"></span><span class="price">$290</span></li>
    <li><span class="item">Full leg</span><span class="leader"></span><span class="price">$490</span></li>
    <li class="gap"></li>
    <li><span class="item">Full back</span><span class="leader"></span><span class="price">$350</span></li>
    <li><span class="item">Shoulders</span><span class="leader"></span><span class="price">$180</span></li>
    <li><span class="item">Nipples</span><span class="leader"></span><span class="price">$60</span></li>
    <li><span class="item">Snail trail</span><span class="leader"></span><span class="price">$50</span></li>
    <li><span class="item">Stomach</span><span class="leader"></span><span class="price">$250</span></li>
    <li><span class="item">Chest</span><span class="leader"></span><span class="price">$250</span></li>
    <li><span class="item">Buttocks</span><span class="leader"></span><span class="price">$200</span></li>
  </ul>
  <h2 class="heading" style="left:53px; top:747px">IPL Photo Rejuvenation</h2>
  <ul class="price-list left" style="top:811px">
    <li><span class="item">Full face</span><span class="leader"></span><span class="price">$350</span></li>
    <li><span class="item">Neck</span><span class="leader"></span><span class="price">$200</span></li>
    <li><span class="item">Face, neck ad décolletage</span><span class="leader"></span><span class="price">$450</span></li>
    <li><span class="item">Spot Treatment</span><span class="leader"></span><span class="price">$50</span></li>
  </ul>

  <!-- Panel 2 -->
  <div class="brand" style="left:469px"><span class="brand-name">maren</span><span class="brand-sub">AESTHETICS</span></div>
  <h2 class="heading" style="left:443px; top:176px">WAXING</h2>
  <ul class="price-list mid" style="top:217px">
    <li><span class="item">Eyebrow</span><span class="leader"></span><span class="price">$21</span></li>
    <li><span class="item">Lip</span><span class="leader"></span><span class="price">$15</span></li>
    <li><span class="item">Chin</span><span class="leader"></span><span class="price">$15</span></li>
    <li><span class="item">Sides of face</span><span class="leader"></span><span class="price">$20</span></li>
    <li><span class="item">Underarm</span><span class="leader"></span><span class="price">$20</span></li>
    <li><span class="item">Forearm</span><span class="leader"></span><span class="price">$25</span></li>
    <li><span class="item">Full arm</span><span class="leader"></span><span class="price">$35</span></li>
    <li><span class="item">Lower leg</span><span class="leader"></span><span class="price">$30</span></li>
    <li><span class="item">Upper leg</span><span class="leader"></span><span class="price">$30</span></li>
    <li><span class="item">Full leg</span><span class="leader"></span><span class="price">$50</span></li>
    <li><span class="item">Inner thigh</span><span class="leader"></span><span class="price">$10</span></li>
    <li><span class="item">Snail trail</span><span class="leader"></span><span class="price">$10</span></li>
    <li><span class="item">Bikini</span><span class="leader"></span><span class="price">$30</span></li>
    <li><span class="item">G String</span><span class="leader"></span><span class="price">$40</span></li>
    <li><span class="item">Brazilian</span><span class="leader"></span><span class="price">$50</span></li>
    <li class="gap"></li>
    <li><span class="item">Eyebrow wax and Lip wax</span><span class="leader"></span><span class="price">$30</span></li>
    <li><span class="item">Eyebrow, lip and chin wax</span><span class="leader"></span><span class="price">$45</span></li>
  </ul>
  <h2 class="heading" style="left:443px; top:621px">MENS WAXING</h2>
  <ul class="price-list mid" style="top:656px">
    <li><span class="item">Mono brow</span><span class="leader"></span><span class="price">$5</span></li>
    <li><span class="item">Eyebrow</span><span class="leader"></span><span class="price">$21</span></li>
    <li><span class="item">Neck</span><span class="leader"></span><span class="price">$20</span></li>
    <li><span class="item">Full back</span><span class="leader"></span><span class="price">$45</span></li>
    <li><span class="item">Chest and Abdomen</span><span class="leader"></span><span class="price">$45</span></li>
  </ul>
  <h2 class="heading" style="left:443px; top:776px">TINTING</h2>
  <ul class="price-list mid" style="top:814px">
    <li><span class="item">Eyelash Tint</span><span class="leader"></span><span class="price">$25</span></li>
    <li><span class="item">Lash Lift and Tint</span><span class="leader"></span><span class="price">$80</span></li>
    <li><span class="item">Henna eyebrows and wax</span><span class="leader"></span><span class="price">$80</span></li>
    <li><span class="item">Eyelash Tint and brow wax</span><span class="leader"></span><span class="price">$40</span></li>
  </ul>

  <!-- Panel 3 -->
  <div class="brand" style="left:860px"><span class="brand-name">maren</span><span class="brand-sub">AESTHETICS</span></div>
  <h2 class="heading" style="left:830px; top:176px">TINTING</h2>
  <ul class="price-list right" style="top:217px">
    <li><span class="item">Eyelash Tint</span><span class="leader"></span><span class="price">$25</span></li>
    <li><span class="item">Lash Lift and Tint</span><span class="leader"></span><span class="price">$80</span></li>
    <li><span class="item">Henna eyebrows and wax</span><span class="leader"></span><span class="price">$80</span></li>
    <li><span class="item">Eyelash Tint and brow wax</span><span class="leader"></span><span class="price">$40</span></li>
  </ul>
  <ul class="price-list treatments">
    <li><span class="item">Maren Mini Facial</span><span class="leader"></span><span class="price">$80</span><span class="duration">40min</span></li>
    <li><span class="item">Maren Deluxe Facial</span><span class="leader"></span><span class="price">$110</span><span class="duration">1 hour</span></li>
    <li><span class="item">Microdermabrasion</span><span class="leader"></span><span class="price">$125</span><span class="duration"></span></li>
    <li><span class="item">Mini Micro</span><span class="leader"></span><span class="price">$80</span><span class="duration"></span></li>
  </ul>
  <p class="injectables">Wrinkle Relaxers $175 per area<br>(Crows, frown lines, forehead lines)<br>or all 3 areas for $450, $50 minor areas<br>(Gummy smile, brow lift, bunny lines)</p>

  <div class="photo" role="img" aria-label="Portrait photo of a smiling woman with hands on her cheeks"></div>
  <div class="skin-strip" role="img" aria-label="Continuation of the portrait photo"></div>
  <p class="fillers-band">Dermal Fillers and Lip Fillers $500 per ml</p>

</main>
</body>
</html>
```